TALMORK

The business want a professional looking business card. We have a scetch we will add but want the extra upgrade, and would like more suggestions for variations of our business cards.

```html
<!DOCTYPE html>
<html lang="en">
<head>
<meta charset="utf-8">
<title>TALMORK Business Card</title>
<link rel="stylesheet" href="https://fonts.googleapis.com/css2?family=Playfair+Display:wght@700&family=Montserrat:wght@400;500&display=swap">
<style>
  :root {
    --canvas-bg: #3a3a3a;
    --card-black: #121212;
    --gold: #d4a52e;
    --gold-light: #f3d27a;
    --gold-dark: #a8781a;
    --text-white: #f2f2f2;
    --silver: #d8d8d8;
  }
  * { margin: 0; padding: 0; box-sizing: border-box; }
  html, body { width: 1200px; height: 875px; overflow: hidden; }
  body {
    background: var(--canvas-bg);
    position: relative;
    font-family: "Montserrat", sans-serif;
  }
  .card {
    position: absolute;
    top: 288px;
    width: 520px;
    height: 300px;
    border-radius: 22px;
    background: var(--card-black);
    border-bottom: 2px solid var(--gold);
    box-shadow: 0 18px 40px rgba(0,0,0,0.45);
    overflow: hidden;
  }
  .card--back { left: 50px; }
  .card--front { left: 630px; }

  .pattern-field {
    position: absolute;
    inset: 0;
    background: linear-gradient(110deg, #8c8c8c 0%, #4a4a4a 28%, #1e1e1e 52%, #121212 100%);
  }
  .back-name {
    position: absolute;
    left: 0; right: 0; top: 136px;
    text-align: center;
    font-family: "Playfair Display", serif;
    font-weight: 700;
    font-size: 20px;
    letter-spacing: 3px;
    color: var(--gold);
  }

  .brand-mark {
    position: absolute;
    right: 38px;
    top: 34px;
    width: 120px;
    height: 120px;
    border-radius: 50%;
    background: radial-gradient(circle at 35% 30%, var(--gold-light), var(--gold) 55%, var(--gold-dark));
  }
  .wordmark {
    position: absolute;
    left: 40px;
    top: 62px;
    font-family: "Playfair Display", serif;
    font-weight: 700;
    font-size: 42px;
    letter-spacing: 4px;
    color: var(--gold);
  }
  .since {
    position: absolute;
    left: 130px;
    top: 118px;
    font-family: "Montserrat", sans-serif;
    font-weight: 500;
    font-size: 10px;
    letter-spacing: 6px;
    color: var(--gold);
  }
  .person-name {
    position: absolute;
    left: 70px;
    top: 150px;
    font-family: "Playfair Display", serif;
    font-weight: 700;
    font-size: 25px;
    color: var(--gold);
  }
  .person-title {
    position: absolute;
    left: 72px;
    top: 184px;
    font-size: 13px;
    color: var(--text-white);
  }
  .contact-list {
    position: absolute;
    left: 84px;
    top: 214px;
    list-style: none;
  }
  .contact-list li {
    display: flex;
    align-items: center;
    gap: 8px;
    font-size: 12.5px;
    line-height: 22px;
    color: var(--text-white);
  }
  .contact-icon { width: 11px; height: 11px; fill: var(--gold); flex: none; }
</style>
</head>
<body>

  <section class="card card--back">
    <div class="pattern-field" role="img" aria-label="Repeating brand-symbol pattern, fading from silver to black"></div>
    <div class="back-name">TALMORK</div>
  </section>

  <section class="card card--front">
    <div class="brand-mark"></div>
    <div class="wordmark">TALMORK</div>
    <div class="since">SINCE 2026</div>

    <div class="person-name">Erik Morten Halvorsen</div>
    <div class="person-title">CEO &amp; Founder</div>

    <ul class="contact-list">
      <li>
        <svg class="contact-icon" viewBox="0 0 24 24"><path d="M6.6 10.8a15.1 15.1 0 0 0 6.6 6.6l2.2-2.2a1 1 0 0 1 1-.25 11.4 11.4 0 0 0 3.6.57 1 1 0 0 1 1 1V20a1 1 0 0 1-1 1A17 17 0 0 1 3 4a1 1 0 0 1 1-1h3.5a1 1 0 0 1 1 1c0 1.25.2 2.45.57 3.57a1 1 0 0 1-.25 1z"/></svg>
        004791234560
      </li>
      <li>
        <svg class="contact-icon" viewBox="0 0 24 24"><path d="M2 5h20v14H2z M2 5l10 8 10-8" fill="none" stroke="#d4a52e" stroke-width="2.4"/></svg>
        contact@talmork.llc
      </li>
      <li>
        <svg class="contact-icon" viewBox="0 0 24 24"><circle cx="12" cy="12" r="10" fill="none" stroke="#d4a52e" stroke-width="2.2"/><path d="M2 12h20M12 2c3 3 3 17 0 20M12 2c-3 3-3 17 0 20" fill="none" stroke="#d4a52e" stroke-width="1.8"/></svg>
        www.talmork.llc
      </li>
    </ul>
  </section>

</body>
</html>
```